Web Developer Needs a Business Card Design

I need a personal business card design that represents me as a web developer for potential employers. I would like the background to be a dark color on the front for contrast with my logo and name. The back will have all my information along with a smaller version of the logo. I want something with a modern look and feel, not too conservative. This will be used for potential employers and freelance work.

Industry/Entity Type

Business

Contact Information for Business Card

Front should have my logo and name. The back should have all my personal information which would include: name: Tom Varulek, phone: 570-614-3098, email: tomvarulek@quillbox.net, website url: www.tomvarulek.net, logo, web developer.

Font styles to use
Sans Serif

Requirements
Must have
• Must include my logo. The color palette base color will be the logo color.

```html
<!DOCTYPE html>
<html lang="en">
<head>
<meta charset="utf-8">
<title>Tom Varulek – Business Card</title>
<link rel="stylesheet" href="https://fonts.googleapis.com/css2?family=Open+Sans:wght@400;600;700&display=swap">
<style>
  :root {
    --teal: #5fb8a5;
    --teal-pale: #d8efe9;
    --paper: #f7f7f6;
    --ink: #1c1c1c;
    --stage: #e9e7e3;
  }
  * { box-sizing: border-box; margin: 0; padding: 0; }
  html, body { width: 1200px; height: 902px; overflow: hidden; }
  body {
    background: var(--stage);
    font-family: "Open Sans", sans-serif;
    position: relative;
  }
  .card {
    position: absolute;
    left: 250px;
    width: 700px;
    height: 400px;
    background: var(--paper);
    overflow: hidden;
    box-shadow: 0 2px 10px rgba(0,0,0,.12);
  }
  .card--front { top: 34px; }
  .card--back { top: 468px; }

  /* front */
  .front-pattern {
    position: absolute; inset: 0;
    background: radial-gradient(circle at 50% 50%, var(--teal-pale), #eef7f4 70%);
  }
  .front-name {
    position: absolute; inset: 0;
    display: flex; align-items: center; justify-content: center;
    font-weight: 700; font-size: 66px; color: var(--ink); letter-spacing: .5px;
  }

  /* back */
  .band { position: absolute; background: var(--teal); }
  .band--upper { left: 50%; right: 0; top: 48px; height: 104px; }
  .band--lower { left: 0; right: 50%; top: 128px; height: 120px; }
  .mark {
    position: absolute; left: 350px; top: 148px;
    width: 188px; height: 188px; margin: -94px 0 0 -94px;
    border-radius: 50%; background: var(--paper);
    display: flex; align-items: center; justify-content: center;
  }
  .mark__ring {
    width: 150px; height: 150px; border-radius: 50%;
    border: 6px solid var(--teal);
    display: flex; align-items: center; justify-content: center;
    text-align: center;
    font-weight: 600; font-size: 20px; line-height: 1.15; color: var(--teal);
  }
  .identity {
    position: absolute; left: 56px; top: 282px; width: 280px;
  }
  .identity__name {
    font-weight: 400; font-size: 38px; color: var(--teal); line-height: 1;
  }
  .identity__role {
    font-size: 19px; color: var(--ink); text-align: right; margin-top: 2px;
  }
  .divider {
    position: absolute; left: 366px; top: 262px; width: 2px; height: 104px;
    background: var(--ink);
  }
  .contacts {
    position: absolute; left: 392px; top: 268px;
    list-style: none;
  }
  .contacts li {
    display: flex; align-items: center; gap: 12px;
    font-size: 19px; color: var(--ink); height: 32px;
  }
  .contacts svg { width: 18px; height: 18px; flex: none; }
</style>
</head>
<body>
  <section class="card card--front" aria-label="Card front">
    <div class="front-pattern" role="img" aria-label="Repeating pattern of the personal logo mark in teal rings"></div>
    <div class="front-name">Tom Varulek</div>
  </section>

  <section class="card card--back" aria-label="Card back">
    <div class="band band--upper"></div>
    <div class="band band--lower"></div>
    <div class="mark"><div class="mark__ring">Tom<br>Varulek</div></div>

    <div class="identity">
      <div class="identity__name">Tom Varulek</div>
      <div class="identity__role">web developer</div>
    </div>
    <div class="divider"></div>

    <ul class="contacts">
      <li>
        <svg viewBox="0 0 18 18" aria-hidden="true"><rect width="18" height="18" fill="#5fb8a5"/><path d="M5 4h3l1 3-2 1a7 7 0 0 0 3 3l1-2 3 1v3c-6 1-10-4-9-9z" fill="#fff"/></svg>
        570-614-3098
      </li>
      <li>
        <svg viewBox="0 0 18 18" aria-hidden="true"><rect width="18" height="18" fill="#5fb8a5"/><circle cx="9" cy="9" r="5" fill="none" stroke="#fff" stroke-width="1.4"/><path d="M4 9h10M9 4c-2.5 3-2.5 7 0 10M9 4c2.5 3 2.5 7 0 10" fill="none" stroke="#fff" stroke-width="1.1"/></svg>
        www.tomvarulek.net
      </li>
      <li>
        <svg viewBox="0 0 18 18" aria-hidden="true"><rect width="18" height="18" fill="#5fb8a5"/><rect x="4" y="5.5" width="10" height="7" fill="#fff"/><path d="M4 5.5l5 4 5-4" fill="none" stroke="#5fb8a5" stroke-width="1.1"/></svg>
        tomvarulek@quillbox.net
      </li>
    </ul>
  </section>
</body>
</html>
```